We need a redesign of our current website: www.halvenridgegroup.com. Halvenridge Group is a fully integrated hospitality development, management, and investment firm. We strive for leadership in each of our segments by building quality assets, exacting high standards of customer service, and focusing on returns for our investors and partners.

It is our mission to provide our guests an exceptional lodging experience; our clients an unsurpassed level of management in their properties; and create positive returns for our investors and partners. We achieve our mission via a company culture of transparency, ownership of our actions, and accountability for our results.

Target Market(s)

hotel owners, hotel developers, hotel investors, bankers

Industry/Entity Type

Hospitality

Requirements
Must have
• Our logo has to be there along with the quote and the ability to convey the following quote off of our current website: "Halvenridge was founded on the principles of integrity, honesty, loyalty, and trust. These convictions embody our company at every level, and show in every action."

```html
<!DOCTYPE html>
<html lang="en">
<head>
<meta charset="utf-8">
<title>Halvenridge Group</title>
<link rel="stylesheet" href="https://fonts.googleapis.com/css2?family=Cinzel:wght@400;700&family=Open+Sans:ital,wght@0,400;0,600;1,400&display=swap">
<style>
:root{
  --orange:#f0a20a;
  --orange-deep:#e08e00;
  --orange-text:#f39c12;
  --ink:#1e1e1e;
  --body:#3c3c3c;
  --muted:#666;
  --rule:#d9d9d9;
  --paper:#fff;
  --footer:#000;
  --footer-text:#a9a9a9;
  --social:#2f7fd6;
}
*{box-sizing:border-box;margin:0;padding:0}
html,body{width:843px;height:1200px;overflow:hidden;background:var(--paper)}
body{position:relative;font-family:"Open Sans",Arial,sans-serif;color:var(--body)}
.abs{position:absolute}
a{text-decoration:none}

/* header */
.site-header{left:0;top:0;width:843px;height:134px;background:linear-gradient(#fff 0%,#fff 55%,#ececec 100%)}
.top-strip{left:0;top:0;width:843px;height:5px;background:#e3e3e3}
.account-tab{left:635px;top:5px;width:168px;height:21px;background:#e6e6e6;border-radius:0 0 8px 8px;font-size:9.5px;color:#666;text-align:center;line-height:19px}
.brand{left:35px;top:50px;display:flex;align-items:center;gap:10px}
.brand-dot{width:50px;height:50px;border-radius:50%;background:var(--orange-deep)}
.brand-name{font-family:"Cinzel",Georgia,serif;font-weight:700;font-size:17px;color:var(--orange-deep);line-height:1.1;width:170px}
.call-us{left:599px;top:47px;font-family:"Cinzel",Georgia,serif;font-size:15px;color:var(--orange-deep);white-space:nowrap}
.call-us b{font-weight:700}
.nav-item{position:absolute;top:101px;font-size:12.5px;color:var(--ink);transform:translateX(-50%)}
.nav-item.is-active{background:var(--orange);color:#fff;border-radius:8px;width:64px;height:20px;text-align:center;line-height:20px;transform:none}
.nav-sep{position:absolute;top:98px;width:1px;height:34px;background:#d2d2d2}

/* hero */
.hero{left:0;top:134px;width:843px;height:277px;background:linear-gradient(90deg,#eb9a06 0%,#f4b21d 45%,#f3ad17 75%,#ee9f0b 100%);overflow:hidden}
.hero-building{left:240px;top:0;width:320px;height:277px;background:linear-gradient(180deg,rgba(255,225,140,.55),rgba(250,200,80,.35))}
.hero-person{left:530px;top:10px;width:230px;height:267px;background:linear-gradient(180deg,#f3c46a 0%,#f6e6cf 55%,#fbf6ee 100%);border-radius:110px 110px 0 0}
.hero-title{left:70px;top:55px;font-family:"Cinzel",Georgia,serif;color:#1a1a1a;font-size:24px;font-weight:700;letter-spacing:.5px;white-space:nowrap}
.hero-title span{font-weight:400;font-size:17px;color:#fff;letter-spacing:1px}
.hero-marker{left:60px;top:84px}
.hero-text{left:72px;top:93px;width:312px;font-size:8.8px;line-height:15px;color:#fff}
.hero-btn{left:72px;top:179px;width:103px;height:22px;background:#111;color:#fff;font-size:9px;font-weight:600;line-height:22px;padding-left:9px;box-shadow:0 6px 6px -4px rgba(0,0,0,.35);white-space:nowrap}
.hero-arrow{top:99px}

.band{left:0;top:411px;width:843px;height:30px;background:linear-gradient(#ececec,#fff)}

/* content */
.section-title{font-size:14.5px;color:var(--ink);font-weight:400;white-space:nowrap}
.welcome{left:26px;top:441px;width:542px}
.welcome p{font-size:8.9px;line-height:13.3px;margin-top:9px;color:var(--body)}
.welcome .section-title{margin-bottom:11px}
.projects-title{left:26px;top:641px}
.thumb{top:670px;width:170px;height:98px;border:3px solid #fff;box-shadow:0 1px 4px rgba(0,0,0,.45)}
.thumb-1{left:26px;background:linear-gradient(180deg,#6d93c9 0%,#9a7b55 55%,#3a2e22 100%)}
.thumb-2{left:208px;background:linear-gradient(180deg,#3a2418 0%,#7a4a2a 50%,#2a1a12 100%)}
.thumb-3{left:390px;background:linear-gradient(180deg,#2c2b2a 0%,#8f8a83 55%,#cfcac3 100%)}
.services-bar{left:22px;top:793px;width:539px;height:29px;border:1px solid #ddd;border-radius:8px;background:linear-gradient(#fbfbfb,#ececec);font-size:11.5px;font-weight:600;color:#333;padding-left:14px;line-height:28px}
.service-list{list-style:none;width:214px}
.service-list li{font-size:8.6px;line-height:17px;height:18px;border-bottom:1px solid #e3e3e3;padding-left:9px;position:relative;color:#333;white-space:nowrap;overflow:hidden}
.service-list li:last-child{border-bottom:none}
.service-list li::before{content:"";position:absolute;left:0;top:7px;width:3px;height:3px;border-right:1px solid #777;border-top:1px solid #777;transform:rotate(45deg)}
.list-left{left:29px;top:833px}
.list-right{left:270px;top:832px}

/* sidebar */
.sidebar{left:587px;top:443px;width:240px;height:437px;border-left:1px solid #e2e2e2;padding-left:14px}
.sidebar .section-title{margin-bottom:12px}
.news{margin-bottom:17px}
.news h3{font-size:10px;font-weight:400;color:var(--ink);margin-bottom:5px}
.news p{font-size:8.9px;line-height:13.2px;color:#555}
.news .meta{margin-top:4px;font-size:8.9px;font-weight:600;color:var(--orange-text);white-space:nowrap}
.news .meta b{color:var(--ink);font-weight:600}
.news .meta i{font-style:normal;color:var(--orange-text);margin:0 6px}

/* footer */
.site-footer{left:0;top:934px;width:843px;height:266px;background:var(--footer)}
.footer-col{top:962px}
.footer-col h4{font-size:12.5px;font-weight:400;color:#fff;margin-bottom:13px}
.footer-col p{font-size:8.9px;line-height:13.2px;color:var(--footer-text);font-weight:600}
.footer-about{left:30px;width:280px}
.footer-about p+p{margin-top:9px}
.footer-quote{left:353px;width:250px}
.footer-quote p{font-style:italic;font-weight:400}
.footer-quote .author{font-style:normal;font-size:10px;margin-top:10px;color:#bbb}
.footer-contact{left:632px}
.footer-rule{top:952px;width:1px;height:130px;background:#2c2c2c}
.pill{height:22px;border-radius:11px;background:linear-gradient(#555,#333);color:#ccc;font-size:7.5px;text-align:center;line-height:22px;white-space:nowrap}
.pill-about{left:28px;top:1089px;width:108px}
.pill-comments{left:351px;top:1084px;width:108px}
.social{left:635px;top:990px;display:flex;gap:4px}
.social span{width:20px;height:20px;border-radius:4px;background:var(--social)}
.footer-nav{left:33px;top:1166px;font-size:9.5px;color:#ccc;white-space:nowrap}
.footer-nav i{font-style:normal;margin:0 7px}
.copyright{left:575px;top:1166px;font-size:9.5px;color:#ccc;white-space:nowrap}
</style>
</head>
<body>

<header class="abs site-header">
  <div class="abs top-strip"></div>
  <div class="abs account-tab">Register &nbsp;|&nbsp; Log In &nbsp;|&nbsp; Member</div>
  <div class="abs brand">
    <div class="brand-dot"></div>
    <div class="brand-name">Halvenridge Group</div>
  </div>
  <div class="abs call-us">Call us now <b>(555)-214-3780</b></div>
  <nav>
    <a class="nav-item is-active" style="left:310px">Home</a>
    <span class="nav-sep" style="left:397px"></span>
    <a class="nav-item" style="left:441px">Services</a>
    <span class="nav-sep" style="left:498px"></span>
    <a class="nav-item" style="left:548px">Projects</a>
    <span class="nav-sep" style="left:603px"></span>
    <a class="nav-item" style="left:647px">Team</a>
    <span class="nav-sep" style="left:697px"></span>
    <a class="nav-item" style="left:739px">Contact</a>
  </nav>
</header>

<section class="abs hero">
  <div class="abs hero-building" role="img" aria-label="Tinted photo of a modern multi-storey hotel building"></div>
  <div class="abs hero-person" role="img" aria-label="Photo of a smiling businesswoman in a white blouse"></div>
  <h1 class="abs hero-title">Halvenridge <span>Punch Line goes..</span></h1>
  <svg class="abs hero-marker" width="8" height="8" viewBox="0 0 8 8"><path d="M7 0 L0 4 L7 8 Z" fill="#fff"/></svg>
  <p class="abs hero-text">Brightmoor Webworks is a web service company, offering a wide range of services which range from designing and development, that is covering almost all the fields in the best possible way. To be the best we know what and how to present beautifully the working of the client's need and their advantages be highlighted.</p>
  <a class="abs hero-btn">READ MORE HERE &nbsp;›</a>
  <svg class="abs hero-arrow" style="left:21px" width="18" height="50" viewBox="0 0 18 50"><path d="M16 1 L2 25 L16 49" fill="none" stroke="#fff" stroke-width="2"/></svg>
  <svg class="abs hero-arrow" style="left:786px" width="18" height="50" viewBox="0 0 18 50"><path d="M2 1 L16 25 L2 49" fill="none" stroke="#fff" stroke-width="2"/></svg>
</section>
<div class="abs band"></div>

<main>
  <section class="abs welcome">
    <h2 class="section-title">Welcome to Halvenridge Website Mainpage</h2>
    <p>Halvenridge Group is a fully integrated hospitality development, management, and investment firm. We strive for leadership in each of our segments by building quality assets, exacting high standards of customer service, and focusing on returns for our investors and partners.</p>
    <p>It is our mission to provide our guests an exceptional lodging experience; our clients an unsurpassed level of management in their properties; and create positive returns for our investors and partners. We achieve our mission via a company culture of transparency, ownership of our actions, and accountability for our results.</p>
    <p>The only way to success is through the right path and that's what we provide you. None of the other companies has the result we do. So stick to the best that's how you will be the best don't opt for the second best. Our expertise does not limit itself to web development but also it includes Web Hosting, Search Engine Optimization, E-Commerce. We partner hundreds of organization to enhance their business, marketing and profit goals.</p>
  </section>

  <h2 class="abs section-title projects-title">Some of Our Latest Project &amp; Team Work</h2>
  <div class="abs thumb thumb-1" role="img" aria-label="Photo of a lit hotel facade at dusk"></div>
  <div class="abs thumb thumb-2" role="img" aria-label="Photo of a warm wood-panelled hotel bar"></div>
  <div class="abs thumb thumb-3" role="img" aria-label="Photo of a hotel reception desk with guests"></div>

  <div class="abs services-bar">Some of Our Services here</div>
  <ul class="abs service-list list-left">
    <li>Your Services punch line or description goes here</li>
    <li>Services punch line or description goes here</li>
    <li>Your Services punch line or description goes here</li>
    <li>Services punch line or description goes</li>
  </ul>
  <ul class="abs service-list list-right">
    <li>Your Services punch line or description goes here</li>
    <li>Services punch line or description goes here</li>
    <li>Your Services punch line or description goes here</li>
    <li>Services punch line or description goes</li>
  </ul>

  <aside class="abs sidebar">
    <h2 class="section-title">Recent Blog &amp; News</h2>
    <article class="news">
      <h3>Headline Goes here</h3>
      <p>Static website are the which are usually been used and are benefited through the Professionals and Small Companies. The companies with fewer budgets can promote their products and services through the static website and gain a lot.</p>
      <div class="meta">Posted On 20.March.2012<i>|</i><b>READ MORE</b></div>
    </article>
    <article class="news">
      <h3>Headline Goes here</h3>
      <p>Static website are the which are usually been used and are benefited through the Professionals and Small Companies.</p>
      <div class="meta">Posted On 20.March.2012<i>|</i><b>READ MORE</b></div>
    </article>
    <article class="news">
      <h3>Headline Goes here</h3>
      <p>Static website are the which are usually been used and are benefited through the Professionals and Small Companies.</p>
      <div class="meta">Posted On 20.March.2012<i>|</i><b>READ MORE</b></div>
    </article>
    <article class="news">
      <h3>Headline Goes here</h3>
      <p>Static website are the which are usually been used and are benefited through the Professionals and Small Companies.</p>
      <div class="meta">Posted On 20.March.2012<i>|</i><b>READ MORE</b></div>
    </article>
  </aside>
</main>

<footer class="abs site-footer"></footer>
<div class="abs footer-col footer-about">
  <h4>Little About Our Company</h4>
  <p>Brightmoor Webworks is a professional website design company dedicated to provide excellent services. We at Brightmoor Webworks think graphic design as a combination and collaboration of ideas and technology.</p>
  <p>Our Website Design team give an unforgettable impression on the customers and the clients.</p>
</div>
<span class="abs footer-rule" style="left:323px"></span>
<div class="abs footer-col footer-quote">
  <h4>Testimonials</h4>
  <p>"Halvenridge was founded on the principles of integrity, honesty, loyalty, and trust. These convictions embody our company at every level, and show in every action."</p>
  <p class="author">BY AUTHOR NAME</p>
</div>
<span class="abs footer-rule" style="left:611px"></span>
<div class="abs footer-col footer-contact">
  <h4>Get In Touch</h4>
</div>
<div class="abs social" aria-label="Social links"><span></span><span></span><span></span><span></span></div>
<a class="abs pill pill-about">READ MORE ABOUT US</a>
<a class="abs pill pill-comments">VIEW MORE COMMENTS</a>
<nav class="abs footer-nav">Home<i>|</i>Services<i>|</i>Project<i>|</i>Team<i>|</i>Contact</nav>
<p class="abs copyright">copyright © 2012 Company Name &nbsp;|&nbsp; All right reserved</p>

</body>
</html>
```